Bright Step Path Flyer, eyecatching

Hi,
To give you an idea of the business for design purposes, #BrighttStepPath is predominantly a recruitment and people development business, ran by me dedicated to training & assisting others in achieving extra income (pt or f/t) around their current commitments, people also have the opportunity to build their own business brand with my support. My brand colours are Red, White and Black, and I would like to incorporate the following text;

#BrightStepPath

Recruiting now! Start today & start earning!

Would you like an extra income, for…
A holiday?…A new car?…Lifestyle changes?
(Can you put a tick box or something similar adjacent to each)

Are you facing…
Redundancy? Birth of a new child? Hefty bills?

If so, I have the solution.

Contact Yvonne Darcott today: (can you insert the appropriate icon for each of the contact details)
Tel: 07419 604172
Twitter: @Bright_StepPath
Email: Yvonne@brightsteppath-example.co.uk
Facebook: www.socialpage-example.com/yvonbrightsteppath

Target Market(s)

Women aged 25-45 years, possibly busy mums too, wanting to earn additinal income to allow them more choices, be it family time, money, new challenge, meeting new people, personal development

Industry/Entity Type

Health And Wellness

Font styles to use
Serif
Sans Serif
Decorative
Script

Colors
ec1f27
ffffff
000000

Requirements
Must have
• My heels logo, be clear concise and eye catching, I also have the following strap line if you wish to use;
• Empowering other to achieve
• Also I have attached a closeup picture of myself but would ideally only like half my face to appear (leftside) similar to the other picture posted - if you can
Nice to have
• Perhaps adding other forms of graphics, or the 3rd picture I have attached with myself...possibly just the shoes though
Should not have
• Too many colours

```html
<!DOCTYPE html>
<html lang="en">
<head>
<meta charset="utf-8">
<title>Bright Step Path – Recruiting Flyer</title>
<link rel="stylesheet" href="https://fonts.googleapis.com/css2?family=Roboto+Condensed:wght@400;700&family=Ubuntu:wght@400;500&display=swap">
<style>
  :root {
    --page-bg: #e8e5e1;
    --brand-red: #b51f26;
    --brand-red-light: #d87a6d;
    --band-dark: #333333;
    --ink: #1f1f1f;
    --white: #ffffff;
    --cream: #efe9a6;
    --cream-light: #fbf9e9;
    --accent-line: #e8e38a;
    --photo-a: #c9a3b3;
    --photo-b: #8f6f86;
    --social-dot: #2b8fd6;
  }
  * { box-sizing: border-box; margin: 0; padding: 0; }
  html, body { width: 1200px; height: 1200px; overflow: hidden; }
  body { background: var(--page-bg); position: relative; font-family: "Roboto Condensed", sans-serif; }

  .flyer {
    position: absolute; left: 189px; top: 20px;
    width: 822px; height: 1160px; background: var(--white);
    box-shadow: 0 4px 18px rgba(0,0,0,.25); overflow: hidden;
  }

  .hero-photo {
    position: absolute; left: 0; top: 0; width: 822px; height: 291px;
    background: radial-gradient(ellipse at 50% 70%, var(--photo-a) 0%, #b58ea2 45%, var(--photo-b) 100%);
  }
  .brand-name {
    position: absolute; left: 0; top: 32px; width: 100%; text-align: center;
    font-family: "Ubuntu", sans-serif; font-weight: 500; font-size: 54px;
    color: var(--white); letter-spacing: -1.5px;
  }

  .hero-rule { position: absolute; left: 0; top: 291px; width: 822px; height: 4px; background: var(--accent-line); }

  .headline-band {
    position: absolute; left: 0; top: 295px; width: 822px; height: 61px;
    background: var(--band-dark); color: var(--white);
    font-size: 38px; line-height: 61px; text-align: center;
  }

  .reasons {
    position: absolute; left: 0; top: 356px; width: 822px; height: 404px;
    background: radial-gradient(ellipse at 50% 55%, var(--cream-light) 0%, #f6f2cf 45%, var(--cream) 100%);
  }
  .reasons-title {
    position: absolute; left: 0; width: 100%; text-align: center;
    font-size: 31px; font-weight: 400; color: var(--ink);
  }
  .reasons-title.wish { top: 16px; }
  .reasons-title.facing { top: 222px; }

  .reason { position: absolute; width: 200px; text-align: center; }
  .reason svg { display: block; margin: 0 auto; width: 80px; height: 80px; }
  .reason-label { font-size: 20px; color: var(--ink); margin-top: 8px; letter-spacing: -.3px; }

  .offer {
    position: absolute; left: 0; top: 760px; width: 822px; height: 331px;
    background: var(--brand-red);
  }
  .shoe-art {
    position: absolute; left: 46px; top: 52px; width: 243px; height: 241px;
    border: 6px solid var(--brand-red-light);
    background: linear-gradient(135deg, #ffffff 0%, #f3f0f0 55%, #e7d6d6 100%);
  }
  .offer-heading {
    position: absolute; left: 310px; top: 52px;
    font-size: 40px; font-weight: 400; line-height: 48px; color: var(--white); letter-spacing: -.8px;
  }
  .contact-list { position: absolute; left: 310px; top: 172px; list-style: none; }
  .contact-item {
    display: flex; align-items: center; height: 32px;
    font-size: 23px; color: var(--white); letter-spacing: -.4px; white-space: nowrap;
  }
  .contact-icon { width: 30px; height: 30px; margin-right: 21px; display: flex; align-items: center; justify-content: center; }
  .contact-icon .dot { width: 26px; height: 26px; border-radius: 50%; background: var(--social-dot); }
  .contact-icon .at { font-family: "Ubuntu", sans-serif; font-size: 28px; line-height: 1; }

  .footer-rule { position: absolute; left: 0; top: 1091px; width: 822px; height: 4px; background: var(--brand-red-light); }
  .strapline-band {
    position: absolute; left: 0; top: 1095px; width: 822px; height: 62px;
    background: var(--band-dark); color: var(--white);
    font-family: "Ubuntu", sans-serif; font-size: 25px; line-height: 60px; text-align: center; letter-spacing: .5px;
  }
  .bottom-edge { position: absolute; left: 0; top: 1157px; width: 822px; height: 3px; background: var(--brand-red); }
</style>
</head>
<body>
<main class="flyer">
  <div class="hero-photo" role="img" aria-label="Close-up portrait photograph of the business owner"></div>
  <h1 class="brand-name">Bright Step Path</h1>
  <div class="hero-rule"></div>

  <div class="headline-band">Recruiting now! Start today &amp; start earning!</div>

  <section class="reasons">
    <h2 class="reasons-title wish">Would you like an extra income, for…</h2>

    <div class="reason" style="left:102px;top:72px">
      <svg viewBox="0 0 80 80" aria-hidden="true">
        <circle cx="40" cy="40" r="38" fill="var(--brand-red)" stroke="#d9d3c0" stroke-width="2"/>
        <path d="M40 58 L42 30" stroke="#fff" stroke-width="4" fill="none"/>
        <path d="M42 30 C34 20 24 24 22 30 C30 26 36 28 42 30 C48 20 58 22 60 28 C52 26 46 28 42 30 C40 20 34 16 30 16 C38 18 40 24 42 30" fill="#fff"/>
        <path d="M24 60 Q40 52 56 60 Z" fill="#fff"/>
        <path d="M18 64 Q40 60 62 64" stroke="#fff" stroke-width="2" fill="none"/>
      </svg>
      <p class="reason-label">A holiday?</p>
    </div>
    <div class="reason" style="left:306px;top:72px">
      <svg viewBox="0 0 80 80" aria-hidden="true">
        <circle cx="40" cy="40" r="38" fill="var(--brand-red)" stroke="#d9d3c0" stroke-width="2"/>
        <path d="M22 40 L27 26 Q28 23 32 23 L48 23 Q52 23 53 26 L58 40 Q62 41 62 45 L62 54 L18 54 L18 45 Q18 41 22 40 Z" fill="#fff"/>
        <path d="M27 39 L31 28 L49 28 L53 39 Z" fill="var(--brand-red)"/>
        <rect x="20" y="52" width="9" height="9" rx="2" fill="#fff"/>
        <rect x="51" y="52" width="9" height="9" rx="2" fill="#fff"/>
        <circle cx="26" cy="46" r="3" fill="var(--brand-red)"/>
        <circle cx="54" cy="46" r="3" fill="var(--brand-red)"/>
      </svg>
      <p class="reason-label">A new car?</p>
    </div>
    <div class="reason" style="left:508px;top:72px">
      <svg viewBox="0 0 80 80" aria-hidden="true">
        <circle cx="40" cy="40" r="38" fill="var(--brand-red)" stroke="#d9d3c0" stroke-width="2"/>
        <rect x="20" y="36" width="9" height="22" rx="2" fill="#fff"/>
        <path d="M32 36 L40 22 Q42 16 46 18 Q49 20 47 28 L45 34 L58 34 Q62 35 61 39 L58 54 Q57 58 52 58 L32 58 Z" fill="#fff"/>
      </svg>
      <p class="reason-label">Lifestyle changes?</p>
    </div>

    <h2 class="reasons-title facing">Are you facing…</h2>

    <div class="reason" style="left:102px;top:273px">
      <svg viewBox="0 0 80 80" aria-hidden="true">
        <circle cx="40" cy="40" r="38" fill="var(--brand-red)" stroke="#d9d3c0" stroke-width="2"/>
        <path d="M24 38 A16 16 0 0 1 52 29" stroke="#fff" stroke-width="6" fill="none"/>
        <path d="M56 20 L56 34 L43 33 Z" fill="#fff"/>
        <path d="M56 42 A16 16 0 0 1 28 51" stroke="#fff" stroke-width="6" fill="none"/>
        <path d="M24 60 L24 46 L37 47 Z" fill="#fff"/>
      </svg>
      <p class="reason-label">Redundancy?</p>
    </div>
    <div class="reason" style="left:306px;top:273px">
      <svg viewBox="0 0 80 80" aria-hidden="true">
        <circle cx="40" cy="40" r="38" fill="var(--brand-red)" stroke="#d9d3c0" stroke-width="2"/>
        <circle cx="40" cy="22" r="7" fill="#fff"/>
        <path d="M30 32 L50 32 L58 40 L54 44 L50 40 L50 50 L30 50 L30 40 L26 44 L22 40 Z" fill="#fff"/>
        <path d="M30 52 L38 52 L32 62 L26 58 Z M50 52 L42 52 L48 62 L54 58 Z" fill="#fff"/>
      </svg>
      <p class="reason-label">Birth of a new child?</p>
    </div>
    <div class="reason" style="left:508px;top:273px">
      <svg viewBox="0 0 80 80" aria-hidden="true">
        <circle cx="40" cy="40" r="38" fill="var(--brand-red)" stroke="#d9d3c0" stroke-width="2"/>
        <path d="M24 18 L56 16 L58 60 L26 62 Z" fill="#fff" stroke="#6d1014" stroke-width="1.5"/>
        <path d="M30 36 L52 35 M30 41 L52 40 M30 46 L52 45 M30 51 L46 50" stroke="var(--brand-red)" stroke-width="1.5"/>
        <text x="40" y="30" text-anchor="middle" font-family="Georgia, serif" font-size="10" font-weight="700" fill="var(--brand-red)">BILL</text>
      </svg>
      <p class="reason-label">Hefty bills?</p>
    </div>
  </section>

  <section class="offer">
    <div class="shoe-art" role="img" aria-label="Sketch illustration of a pair of high-heeled shoes with red soles"></div>
    <h2 class="offer-heading">If so, I have the solution.<br>Contact Yvonne Darcott today</h2>
    <ul class="contact-list">
      <li class="contact-item">
        <span class="contact-icon">
          <svg viewBox="0 0 30 24" width="30" height="24" aria-hidden="true">
            <path d="M2 8 Q15 0 28 8 L26 12 L21 10 L21 7 Q15 5 9 7 L9 10 L4 12 Z" fill="#fff"/>
            <path d="M8 13 L22 13 L25 22 L5 22 Z" fill="#fff"/>
            <circle cx="15" cy="17" r="2.5" fill="var(--brand-red)"/>
          </svg>
        </span>07419 604172
      </li>
      <li class="contact-item"><span class="contact-icon"><span class="dot"></span></span>@Bright_StepPath</li>
      <li class="contact-item"><span class="contact-icon"><span class="at">@</span></span>Yvonne@brightsteppath-example.co.uk</li>
      <li class="contact-item"><span class="contact-icon"><span class="dot"></span></span>www.socialpage-example.com/yvonbrightsteppath</li>
    </ul>
  </section>

  <div class="footer-rule"></div>
  <div class="strapline-band">Empowering others to achieve</div>
  <div class="bottom-edge"></div>
</main>
</body>
</html>
```